Computer consultant business card

Bexil Software is a newly started computer consulting company. It's a small one-man company that provides mostly Vornix applications but also websites in collaboration with designers. I'm running this company on the side of full time university studies.

I want the final design to be clean and memorable. Be creative! :)

Some inspiration:
http://www.pixelmarta.com/design/48317
http://www.pixelmarta.com/design/2739164/business-card-design-by-frostlynk
http://www.pixelmarta.com/design/604281/business-card-design-by-koralind-vestrabanu

See attachment for my company logo.
Updates

I would like to thank everyone for submitting! I'll need a couple of days to review and ultimately select a design.

Target Market(s)

Non-technical entrepreneurs and small companies.

Industry/Entity Type

University

Requirements
Must have
• My company logo.
In any way, both colors from my logo.
First- and last name, e-mail and phone number.
Double-sided design.
Nice to have
• Something creative with the symbol in my logo

```html
<!DOCTYPE html>
<html lang="en">
<head>
<meta charset="UTF-8">
<title>Vaxlo – Business Card</title>
<link href="https://fonts.googleapis.com/css2?family=Poppins:wght@600&family=Tinos&family=Oswald:wght@600&family=Arimo&display=swap" rel="stylesheet">
<style>
  :root {
    --stage-light: #d9d9d9;
    --stage-dark: #6e6e6e;
    --frame: #2a2b2d;
    --panel: #e8e9eb;
    --accent: #3a64b0;
    --rule: #f4f4f4;
    --ink: #2a2b2d;
    --ink-soft: #4a4b4d;
  }
  * { margin: 0; padding: 0; box-sizing: border-box; }
  html, body { width: 1200px; height: 787px; overflow: hidden; }
  body {
    background: radial-gradient(ellipse at 50% 45%, var(--stage-light) 0%, #b3b3b3 55%, var(--stage-dark) 100%);
    position: relative;
  }
  .card {
    position: absolute;
    top: 244px;
    width: 520px;
    height: 300px;
    box-shadow: 0 10px 24px rgba(0,0,0,.25);
  }
  .card--front { left: 50px; }
  .card--back { left: 630px; }
  .card__frame { position: absolute; inset: 0; width: 100%; height: 100%; }

  .brand { position: absolute; display: flex; align-items: center; gap: 12px; }
  .brand__dot { width: 44px; height: 44px; border-radius: 50%; background: var(--accent); flex: none; }
  .brand__name {
    font-family: "Poppins", sans-serif; font-weight: 600;
    font-size: 52px; line-height: 1; color: var(--ink); letter-spacing: -1px;
  }

  .front__brand { left: 150px; top: 92px; }
  .front__name {
    position: absolute; left: 212px; top: 158px;
    font-family: "Tinos", serif; font-size: 22px; color: var(--ink);
  }
  .front__role {
    position: absolute; left: 212px; top: 184px;
    font-family: "Tinos", serif; font-size: 14px; color: var(--ink);
  }

  .back__brand { left: 58px; top: 62px; }
  .back__brand .brand__dot { width: 36px; height: 36px; }
  .back__brand .brand__name { font-size: 42px; }
  .back__title {
    position: absolute; left: 112px; top: 112px;
    font-family: "Tinos", serif; font-size: 17px; line-height: 1.05;
    letter-spacing: 1.5px; color: var(--ink); text-align: center;
  }
  .back__person { position: absolute; right: 92px; top: 40px; text-align: left; }
  .back__person-name {
    font-family: "Oswald", sans-serif; font-weight: 600;
    font-size: 19px; color: var(--ink); letter-spacing: .5px;
  }
  .back__person-role { font-family: "Arimo", sans-serif; font-size: 9px; color: var(--ink-soft); }

  .contact-list {
    position: absolute; left: 330px; top: 160px; list-style: none;
    font-family: "Arimo", sans-serif; font-size: 10.5px; color: var(--ink-soft);
  }
  .contact-list__item { display: flex; align-items: center; gap: 8px; height: 20px; }
  .contact-list__icon { width: 11px; height: 11px; fill: var(--ink); }
</style>
</head>
<body>

<section class="card card--front" aria-label="Business card front">
  <svg class="card__frame" viewBox="0 0 520 300" aria-hidden="true">
    <rect width="520" height="300" fill="var(--frame)"/>
    <polygon points="400,0 520,0 520,100" fill="var(--accent)"/>
    <line x1="390" y1="0" x2="520" y2="108" stroke="var(--rule)" stroke-width="3"/>
    <polygon points="0,190 0,300 130,300" fill="var(--accent)"/>
    <line x1="0" y1="182" x2="140" y2="300" stroke="var(--rule)" stroke-width="3"/>
    <rect x="36" y="24" width="450" height="250" fill="var(--panel)"/>
  </svg>
  <div class="brand front__brand">
    <span class="brand__dot"></span>
    <span class="brand__name">vaxlo</span>
  </div>
  <p class="front__name">Your Name</p>
  <p class="front__role">Company Position</p>
</section>

<section class="card card--back" aria-label="Business card back">
  <svg class="card__frame" viewBox="0 0 520 300" aria-hidden="true">
    <rect width="520" height="300" fill="var(--frame)"/>
    <polygon points="400,0 520,0 520,100" fill="var(--accent)"/>
    <line x1="390" y1="0" x2="520" y2="108" stroke="var(--rule)" stroke-width="3"/>
    <polygon points="0,190 0,300 130,300" fill="var(--accent)"/>
    <line x1="0" y1="182" x2="140" y2="300" stroke="var(--rule)" stroke-width="3"/>
    <rect x="36" y="24" width="450" height="250" fill="var(--panel)"/>
  </svg>
  <div class="brand back__brand">
    <span class="brand__dot"></span>
    <span class="brand__name">vaxlo</span>
  </div>
  <p class="back__title">MANAGING<br>DIRECTOR</p>
  <div class="back__person">
    <p class="back__person-name">JOHN DOE</p>
    <p class="back__person-role">Graphic Designer</p>
  </div>
  <ul class="contact-list">
    <li class="contact-list__item">
      <svg class="contact-list__icon" viewBox="0 0 12 12" aria-hidden="true"><path d="M3 0h3l1 3-2 1a6 6 0 0 0 3 3l1-2 3 1v3c0 1-1 2-2 2A10 10 0 0 1 0 2c0-1 1-2 2-2z"/></svg>
      +(000) 1234 5678
    </li>
    <li class="contact-list__item">
      <svg class="contact-list__icon" viewBox="0 0 12 12" aria-hidden="true"><path d="M3 0h3l1 3-2 1a6 6 0 0 0 3 3l1-2 3 1v3c0 1-1 2-2 2A10 10 0 0 1 0 2c0-1 1-2 2-2z"/></svg>
      +(000) 1234 5679
    </li>
    <li class="contact-list__item">
      <svg class="contact-list__icon" viewBox="0 0 12 12" aria-hidden="true"><path d="M0 2h12v8H0z M1 3l5 4 5-4" fill="none" stroke="var(--ink)" stroke-width="1.2"/></svg>
      email@yourdomain.com
    </li>
    <li class="contact-list__item">
      <svg class="contact-list__icon" viewBox="0 0 12 12" aria-hidden="true"><circle cx="6" cy="6" r="5.3" fill="none" stroke="var(--ink)" stroke-width="1.2"/><path d="M0.7 6h10.6M6 0.7c-3 3-3 7.6 0 10.6M6 0.7c3 3 3 7.6 0 10.6" fill="none" stroke="var(--ink)" stroke-width="1"/></svg>
      www.yourwebsite.com
    </li>
  </ul>
</section>

</body>
</html>
```